Our Company is Harbourline Lot Planners and we service the whole Perth Metro region. We want our flyer to grab the potential clients attention and inform them of their potential opportunity to subdivide their residential property. We would like the flyer to show our logo, contact details website and maybe one eye catching, engaging picture/photo. If the Flyer could follow the same colours as our logo that would be great. Are we able to have a A5 size flyer front and back? maybe our contact information on the back? and other services that we offer?
A lot of our potential clients aren't aware their house/land is sub dividable, or even know how to do a subdivision. We would like our flyer to educate the average residential home owner of the potential of their property and make the idea of subdividing seem and easy and accessible. Something along the lines of "Looking to Subdivide? Not sure if your property is sub-dividable? Call us now for a obligation free assessment of your property." or maybe "Subdividing you property is easier than you might think..."
We would like to advertise that we offer:-
Free Subdivision feasibility analysis of your property,
Project Management: We offer full Project Management from start to finish ensuring a hassle free subdivision (or something along those lines)-
New title's application
Updates

Target Market(s)

Residential Home owners with the potential to subdivide their property.

Industry/Entity Type

Surveyor

Colors
f78f20
c3c3c3
3176b5

Requirements
Must have
• Simple, clutter free design offering the idea of subdividing as a new, accessible opportunity to the average homeowner.

```html
<!DOCTYPE html>
<html lang="en">
<head>
<meta charset="utf-8">
<title>Harbourline Lot Planners – Flyer</title>
<link rel="stylesheet" href="https://fonts.googleapis.com/css2?family=Lato:wght@400;700&family=Roboto+Condensed:wght@700&display=swap">
<style>
  :root {
    --navy: #1b2a40;
    --navy-deep: #14202f;
    --orange: #ee5a2b;
    --orange-light: #f47a35;
    --orange-dark: #d9461f;
    --grey: #6b6f74;
    --white: #ffffff;
    --sky: #a9c4dc;
    --field: #8c9a5a;
    --soil: #c9956a;
  }
  * { box-sizing: border-box; margin: 0; padding: 0; }
  html, body { width: 907px; height: 1200px; overflow: hidden; background: #e9e9e9; }
  .flyer { position: relative; width: 907px; height: 1200px; overflow: hidden; font-family: "Lato", sans-serif; }
  .flyer-shapes { position: absolute; inset: 0; }

  .brand-box {
    position: absolute; left: 291px; top: 96px; width: 324px; height: 166px;
    background: var(--white); border: 8px solid var(--orange); border-radius: 24px;
    outline: 5px solid var(--navy);
    display: flex; flex-direction: column; align-items: center; justify-content: center;
  }
  .brand-name {
    font-family: "Lato", sans-serif; font-weight: 700; color: var(--navy);
    font-size: 36px; line-height: 1.1; text-align: center;
  }

  .headline {
    position: absolute; left: 0; width: 907px; top: 586px; text-align: center;
    font-family: "Roboto Condensed", sans-serif; font-weight: 700;
    font-variant: small-caps; font-size: 50px; letter-spacing: 0.5px; color: var(--orange);
  }
  .headline .muted { color: var(--grey); }
  .intro {
    position: absolute; left: 0; width: 907px; top: 656px; text-align: center;
    font-size: 20px; line-height: 27px; color: var(--navy-deep);
  }

  .services-tab {
    position: absolute; left: 272px; top: 770px; width: 362px; height: 96px;
    background: var(--navy); border-radius: 0 0 22px 22px;
    display: flex; align-items: center; justify-content: center; padding-top: 12px;
  }
  .services-title {
    font-family: "Roboto Condensed", sans-serif; font-weight: 700; font-size: 42px; color: var(--orange-light);
  }

  .services-list {
    position: absolute; top: 890px; left: 52px; right: 20px;
    display: grid; grid-template-columns: 266px 298px 1fr; list-style: none;
  }
  .services-list ul { list-style: none; }
  .services-list li {
    position: relative; padding-left: 19px; color: var(--white);
    font-size: 18px; line-height: 31px; white-space: nowrap;
  }
  .services-list li::before {
    content: ""; position: absolute; left: 0; top: 12px; width: 8px; height: 8px;
    border-radius: 50%; background: var(--white);
  }

  .contact { position: absolute; left: 240px; width: 430px; top: 1094px; text-align: center; }
  .contact-call {
    font-family: "Roboto Condensed", sans-serif; font-weight: 700; font-size: 36px; color: var(--white);
  }
  .contact-call .label { color: var(--orange-light); }
  .contact-web { margin-top: 10px; font-size: 19px; letter-spacing: 5px; color: var(--white); }

  .surveyor-photo {
    position: absolute; left: 708px; top: 1010px; width: 199px; height: 190px;
    background: linear-gradient(160deg, #8fa3b2 0%, #4d8a84 30%, #e9733a 60%, #2f4f86 100%);
    border-radius: 60px 0 0 0;
  }
</style>
</head>
<body>
<main class="flyer">
  <svg class="flyer-shapes" viewBox="0 0 907 1200" width="907" height="1200" aria-hidden="false">
    <defs>
      <linearGradient id="orangeField" x1="0" y1="0" x2="1" y2="0">
        <stop offset="0" stop-color="var(--orange-dark)"/>
        <stop offset="0.5" stop-color="var(--orange-light)"/>
        <stop offset="1" stop-color="var(--orange-dark)"/>
      </linearGradient>
      <linearGradient id="siteScene" x1="0" y1="0" x2="0" y2="1">
        <stop offset="0" stop-color="#c9dced"/>
        <stop offset="0.45" stop-color="var(--sky)"/>
        <stop offset="0.6" stop-color="var(--field)"/>
        <stop offset="0.78" stop-color="#a4865a"/>
        <stop offset="1" stop-color="var(--soil)"/>
      </linearGradient>
    </defs>

    <rect class="field-orange" width="907" height="1200" fill="url(#orangeField)"/>
    <path class="top-navy" d="M0,0 H907 V660 Q453,930 0,680 Z" fill="var(--navy)"/>
    <path class="white-lens" d="M0,484 Q453,763 907,466 V646 Q453,905 0,665 Z" fill="var(--white)"/>
    <path class="photo-ring" d="M0,330 Q453,-130 907,330 V452 Q453,735 0,470 Z" fill="var(--orange)"/>
    <path class="site-photo" role="img" aria-label="Photo of a loader clearing a residential subdivision site under a blue sky"
          d="M0,345 Q453,-115 907,345 V440 Q453,711 0,458 Z" fill="url(#siteScene)"/>

    <path class="footer-rule" d="M0,1166 Q350,996 907,1036 V1050 Q350,1010 0,1180 Z" fill="var(--white)"/>
    <path class="footer-navy" d="M0,1180 Q350,1010 907,1050 V1200 H0 Z" fill="var(--navy)"/>
  </svg>

  <div class="brand-box">
    <div class="brand-name">Harbourline<br>Lot Planners</div>
  </div>

  <h1 class="headline">We service The Whole <span class="muted">of Perth Metro</span></h1>
  <p class="intro">First time subdividing? no worries! we offer full Project Management<br>from start to finish ensuring a hassle free subdivision</p>

  <div class="services-tab"><h2 class="services-title">Our Services</h2></div>

  <div class="services-list">
    <ul>
      <li>Te veniam erroribus vis</li>
      <li>Veri quodsi eruditi vim ei</li>
      <li>Eum ex debitis ocurreret</li>
      <li>Virtute fuisset nam an</li>
    </ul>
    <ul>
      <li>Iisque similique id nam</li>
      <li>Ius an timeam mediocrem</li>
      <li>Vim moderatius suscipiantur</li>
      <li>Pri legere moderatius ad</li>
    </ul>
    <ul>
      <li>His harum consulatu id</li>
      <li>Sit euripidis disputando et</li>
      <li>Ius saperet vocibus an</li>
      <li>Ei has laboramus vituperata</li>
    </ul>
  </div>

  <div class="contact">
    <p class="contact-call"><span class="label">Call now</span> - 0412 555 018</p>
    <p class="contact-web">www.harbourlinelots.com.au</p>
  </div>

  <div class="surveyor-photo" role="img" aria-label="Photo of a surveyor in a high-visibility vest using a total station"></div>
</main>
</body>
</html>
```